Social Media Graphics - Oakline Push REVISED

Create 6-7 individual social media graphics (square size) to encourage folks to join our online course called:

The Harvest Ledger Circle
How to Launch a Multi-Million Business From Scratch
Sign Up Today!

IMPORTANT: Make the largest and most prominent text on the graphic be: How to Launch a Multi-Million Business From Scratch

For the color scheme of the graphics, let's try a blue color palette; make sure the graphics appeal to both men and women

Make sure each graphic contains 1 of the 3 pics attached (crop pic as needed); and make sure one of the graphics is all TEXT only.

Target Market(s)

men and women looking to start a business

Industry/Entity Type

Entrepreneurship

Colors
0054AA
0677BA
7BADD7
CADEEF
E8F1F8

Requirements
Must have
• All the text and use the 3 pics provided; one graphic can be all text; Simple, modern design that's easy to read

```html
<!DOCTYPE html>
<html lang="en">
<head>
<meta charset="UTF-8">
<title>How to Launch a Multi-Million Business From Scratch</title>
<link href="https://fonts.googleapis.com/css2?family=Russo+One&family=Montserrat:wght@700&display=swap" rel="stylesheet">
<style>
  :root {
    --blue-deep: #0054AA;
    --blue-mid: #0677BA;
    --blue-soft: #7BADD7;
    --blue-pale: #CADEEF;
    --blue-mist: #E8F1F8;
    --white: #ffffff;
  }
  * { margin: 0; padding: 0; box-sizing: border-box; }
  html, body { width: 1200px; height: 1200px; overflow: hidden; }
  .post {
    position: relative;
    width: 1200px;
    height: 1200px;
    overflow: hidden;
    background: radial-gradient(circle at 30% 35%, #1a6ab0 0%, #0f5ca3 45%, #0a4f93 100%);
  }
  .photo-frame {
    position: absolute;
    inset: 0;
    width: 1200px;
    height: 1200px;
  }
  .headline {
    position: absolute;
    left: 89px;
    top: 92px;
    font-family: "Russo One", sans-serif;
    font-size: 92px;
    line-height: 128px;
    color: var(--white);
    text-transform: uppercase;
    letter-spacing: 1px;
    text-shadow: 0 4px 14px rgba(0, 30, 70, 0.35);
  }
  .course-name {
    position: absolute;
    left: 89px;
    top: 662px;
    font-family: "Montserrat", sans-serif;
    font-weight: 700;
    font-size: 40px;
    color: var(--white);
  }
  .cta {
    position: absolute;
    left: 87px;
    top: 784px;
    width: 358px;
    height: 73px;
    border-radius: 37px;
    background: var(--blue-mist);
    display: flex;
    align-items: center;
    justify-content: center;
    font-family: "Montserrat", sans-serif;
    font-weight: 700;
    font-size: 28px;
    color: var(--blue-deep);
  }
</style>
</head>
<body>
  <main class="post">
    <svg class="photo-frame" viewBox="0 0 1200 1200" aria-hidden="false">
      <defs>
        <linearGradient id="photoTone" x1="0" y1="0" x2="1" y2="1">
          <stop offset="0%" stop-color="#efe9e2"/>
          <stop offset="45%" stop-color="#c9c2bb"/>
          <stop offset="75%" stop-color="#5f6f8c"/>
          <stop offset="100%" stop-color="#3a3f4a"/>
        </linearGradient>
      </defs>
      <circle class="photo-ring" cx="1260" cy="1300" r="888" fill="var(--blue-mid)"/>
      <circle class="speaker-photo" cx="1260" cy="1300" r="860" fill="url(#photoTone)" role="img" aria-label="Photo of two course hosts smiling on stage, one holding a microphone"/>
    </svg>

    <h1 class="headline">How to launch a<br>multi-million<br>business from<br>scratch</h1>
    <p class="course-name">The Harvest Ledger Circle</p>
    <div class="cta">SIGN UP TODAY!</div>
  </main>
</body>
</html>
```